RW Holloway LLC Business Card - Civil Engineering & Consulting Firm

We need a Business Card that is elegant, and masculine.  It is our Professional Civil Engineering & Consulting Company located in San Antonio TX (Not s construction or builder firm- no gears & no tool images please). We provide civil engineering services including  commercial site plans, grading and drainage plans, utility plans, hydraulics and hydrology, land planning, utility coordination, and other general civil engineering services related to commercial and residential development.
We have 2 existing Logos. We would like to convey reliability, strength, trustworthiness and attention to detail.  Blues and orange tones as per logo We are OK with the use of a darker blue in the mix.  We have 2 logo versions - Full Company Name Logo to go on the back of card, & Small Icon Logo for the front w/ personal Info.

Target Market(s)
Architects, Real Estate Developers, Other Strctural Engineers, Surveyers, General Contractors
Industry/Entity Type
Professional Civil Engineering
Contact Information for Business Card
Name, Position, Address, Cell & Office #, email, and company website
Font styles to use
Other font styles liked:
- Avian
Requirements
Should not have
- No Tools, No Gears, no Cranes, or Construction Equipment.

```html
<!DOCTYPE html>
<html lang="en">
<head>
<meta charset="utf-8">
<title>RW Holloway LLC – Business Card</title>
<link href="https://fonts.googleapis.com/css2?family=Montserrat:wght@400;500;600;700&display=swap" rel="stylesheet">
<style>
  :root {
    --backdrop: #3a3a3b;
    --card: #1b1b1c;
    --card-edge: #7fa9d6;
    --blue: #7aaee0;
    --orange: #f0952a;
    --text: #e9e9e9;
    --rule: #4f6e8f;
  }
  * { box-sizing: border-box; margin: 0; padding: 0; }
  html, body { width: 1200px; height: 801px; overflow: hidden; }
  body {
    background: var(--backdrop);
    font-family: "Montserrat", sans-serif;
    display: flex; align-items: center; justify-content: center; gap: 48px;
  }
  .card {
    position: relative;
    width: 540px; height: 308px;
    background: var(--card);
    border-bottom: 3px solid var(--card-edge);
    border-right: 3px solid var(--card-edge);
    box-shadow: 0 18px 40px rgba(0,0,0,.45);
    overflow: hidden;
  }
  /* front */
  .brand {
    position: absolute; top: 52px; left: 0; right: 0;
    text-align: center;
  }
  .brand-name {
    display: inline-flex; align-items: center; gap: 12px;
    font-size: 34px; font-weight: 500; letter-spacing: 4px; color: var(--blue);
  }
  .brand-square { width: 14px; height: 14px; background: var(--orange); }
  .brand-tagline {
    margin-top: 8px;
    font-size: 9px; letter-spacing: 5px; color: var(--orange); text-transform: uppercase;
  }
  .brand-rule { width: 300px; height: 1px; background: var(--rule); margin: 8px auto 0; }
  .person {
    position: absolute; left: 40px; top: 175px; width: 220px;
  }
  .person-name { font-size: 19px; font-weight: 700; color: var(--blue); letter-spacing: .5px; }
  .person-title { font-size: 13px; color: var(--orange); margin: 2px 0 12px 0; }
  .person-address { font-size: 12.5px; color: var(--text); line-height: 1.5; }
  .divider {
    position: absolute; left: 282px; top: 170px; width: 1px; height: 100px; background: var(--rule);
  }
  .contacts {
    position: absolute; left: 302px; top: 172px; list-style: none;
  }
  .contacts li {
    display: flex; align-items: center; gap: 10px;
    font-size: 12.5px; color: var(--text); line-height: 24px;
  }
  .contacts svg { width: 12px; height: 12px; fill: var(--orange); flex: none; }
  /* back */
  .back-pattern {
    position: absolute; inset: 0;
    background: linear-gradient(135deg, #161617 0%, #232324 55%, #2c2c2d 100%);
  }
  .back-brand {
    position: absolute; inset: 0;
    display: flex; align-items: center; justify-content: center; gap: 10px;
    font-size: 22px; font-weight: 500; letter-spacing: 3px; color: var(--blue);
  }
  .back-brand .brand-square { width: 11px; height: 11px; }
</style>
</head>
<body>
  <section class="card card-front">
    <header class="brand">
      <div class="brand-name"><span class="brand-square"></span>RW HOLLOWAY LLC</div>
      <div class="brand-rule"></div>
      <div class="brand-tagline">Consulting Engineers</div>
    </header>
    <div class="person">
      <p class="person-name">DALE CORVIN</p>
      <p class="person-title">President</p>
      <p class="person-address">1840 Harbor Ridge Dr<br>Bayview CA 90412</p>
    </div>
    <div class="divider"></div>
    <ul class="contacts">
      <li><svg viewBox="0 0 12 12"><path d="M3 0h6a1 1 0 0 1 1 1v10a1 1 0 0 1-1 1H3a1 1 0 0 1-1-1V1a1 1 0 0 1 1-1zm0 1.5v8h6v-8z"/></svg>555-210-4187</li>
      <li><svg viewBox="0 0 12 12"><path d="M2.5 0.5l2 2.5-1.2 1.3a7 7 0 0 0 4.4 4.4L9 7.5l2.5 2-1.5 2C5 11 1 7 .5 2z"/></svg>555-210-4190</li>
      <li><svg viewBox="0 0 12 12"><path d="M0 2h12v8H0zm1 1l5 4 5-4"/></svg>info@rwhollowayllc.com</li>
      <li><svg viewBox="0 0 12 12"><circle cx="6" cy="6" r="6"/></svg>www.rwhollowayllc.com</li>
    </ul>
  </section>

  <section class="card card-back">
    <div class="back-pattern" role="img" aria-label="Repeating embossed monogram pattern in dark grey tones"></div>
    <div class="back-brand"><span class="brand-square"></span>RW HOLLOWAY LLC</div>
  </section>
</body>
</html>
```